Telecommunications/Power civil contractor needs business card design

Were a new telecommunications/power underground civil contractor that is looking for a new business card design. Our company colours are silver or grey and orange. Feel free to use the white background logo or the black background logo.

Target Market(s)

Local contractors, utility companies, private sector mining/energy companies, developers.

Industry/Entity Type

Telecommunications

Contact Information for Business Card

Each card will need the following info:
Persons name:
Title:
E-mail:
Phone number:
Shop Address:
Mailing Address:

Requirements
Must have
• Each card will need the following info:
• Persons name:
• Title:
• E-mail:
• Phone number:
• Shop Address:
• Mailing Address:

```html
<!DOCTYPE html>
<html lang="en">
<head>
<meta charset="utf-8">
<title>Trenchline Civil Inc – Business Card</title>
<link rel="stylesheet" href="https://fonts.googleapis.com/css2?family=Source+Sans+3:wght@400;600;700&display=swap">
<style>
  :root {
    --backdrop: #d8d3cb;
    --card-light: #f1f0ee;
    --card-light-edge: #dcdad6;
    --brand-orange: #f26a1b;
    --brand-orange-deep: #cf4e0c;
    --ink-dark: #3a3a3c;
    --ink-light: #ffffff;
    --ink-soft: rgba(255,255,255,0.9);
    --ink-label: rgba(255,255,255,0.72);
  }
  * { margin: 0; padding: 0; box-sizing: border-box; }
  html, body {
    width: 1200px; height: 969px; overflow: hidden;
    background: var(--backdrop);
    font-family: "Source Sans 3", "Helvetica Neue", Arial, sans-serif;
  }
  .card {
    position: absolute; left: 100px; top: 201px;
    width: 1000px; height: 567px;
    border-radius: 34px; overflow: hidden;
    background: linear-gradient(160deg, var(--card-light), var(--card-light-edge));
    box-shadow: 0 18px 40px rgba(0,0,0,0.22);
  }
  .card-art { position: absolute; inset: 0; width: 100%; height: 100%; }
  .person { position: absolute; left: 64px; top: 52px; color: var(--ink-light); }
  .person-name { font-size: 33px; font-weight: 600; line-height: 1.1; }
  .person-title { font-size: 25px; font-weight: 400; color: var(--ink-soft); margin-top: 4px; }
  .addresses { position: absolute; left: 64px; top: 162px; display: flex; flex-direction: column; gap: 14px; }
  .address { font-size: 23px; line-height: 30px; color: var(--ink-soft); font-style: normal; }
  .address-label {
    display: block; font-size: 15px; line-height: 22px; font-weight: 600;
    letter-spacing: 1.5px; text-transform: uppercase; color: var(--ink-label);
  }
  .contact-list { position: absolute; left: 64px; top: 418px; list-style: none; }
  .contact-item {
    display: flex; align-items: center; gap: 14px;
    font-size: 23px; line-height: 36px; color: var(--ink-soft);
  }
  .contact-icon { width: 20px; height: 20px; fill: var(--ink-soft); flex: none; }
  .brand {
    position: absolute; left: 540px; top: 120px; width: 400px;
    display: flex; flex-direction: column; align-items: center; gap: 28px;
  }
  .brand-mark {
    width: 150px; height: 150px; border-radius: 50%;
    border: 10px solid var(--brand-orange);
  }
  .brand-name {
    font-size: 30px; font-weight: 700; color: var(--ink-dark);
    text-align: center; line-height: 1.1; letter-spacing: 1px; white-space: nowrap;
  }
</style>
</head>
<body>
  <div class="card">
    <svg class="card-art" viewBox="0 0 1000 567" preserveAspectRatio="none" aria-hidden="true">
      <defs>
        <linearGradient id="orangePanel" x1="0" y1="0" x2="1" y2="1">
          <stop offset="0" stop-color="var(--brand-orange)"/>
          <stop offset="1" stop-color="var(--brand-orange-deep)"/>
        </linearGradient>
      </defs>
      <path d="M0 0 H600 Q350 280 700 567 H0 Z" fill="url(#orangePanel)"/>
      <path d="M640 0 Q400 270 720 567" fill="none" stroke="var(--brand-orange)" stroke-width="7"/>
      <path d="M600 0 Q350 280 700 567" fill="none" stroke="#ffffff" stroke-width="10" opacity="0.75"/>
    </svg>

    <div class="person">
      <div class="person-name">Dana Whitlock</div>
      <div class="person-title">CEO/Founder</div>
    </div>

    <div class="addresses">
      <address class="address">
        <span class="address-label">Shop</span>
        2140 Birchfield Road<br>
        Fairbanks, Alaska 99712
      </address>
      <address class="address">
        <span class="address-label">Mailing</span>
        PO Box 83021<br>
        Fairbanks, Alaska 99708
      </address>
    </div>

    <ul class="contact-list">
      <li class="contact-item">
        <svg class="contact-icon" viewBox="0 0 24 24" aria-hidden="true"><path d="M6.6 10.8a15.1 15.1 0 0 0 6.6 6.6l2.2-2.2c.3-.3.7-.4 1-.2 1.1.4 2.3.6 3.6.6.6 0 1 .4 1 1V20c0 .6-.4 1-1 1A17 17 0 0 1 3 4c0-.6.4-1 1-1h3.5c.6 0 1 .4 1 1 0 1.3.2 2.5.6 3.6.1.3 0 .7-.2 1z"/></svg>
        907 555 0148
      </li>
      <li class="contact-item">
        <svg class="contact-icon" viewBox="0 0 24 24" aria-hidden="true"><path d="M2 5h20v14H2z M4 7v.5l8 5 8-5V7l-8 5z" fill-rule="evenodd"/></svg>
        dana@trenchlinecivil.com
      </li>
      <li class="contact-item">
        <svg class="contact-icon" viewBox="0 0 24 24" aria-hidden="true"><circle cx="12" cy="12" r="10"/></svg>
        www.trenchlinecivil.com
      </li>
    </ul>

    <div class="brand">
      <div class="brand-mark"></div>
      <div class="brand-name">TRENCHLINE CIVIL INC</div>
    </div>
  </div>
</body>
</html>
```